Harrow Point Metrics Company Website Design and Coding

We want to redesign our existing website so that it is more visually and functionally appealing to prospective clients and potential job candidates. We would like to keep our current color scheme and implement our current logo as well. We have a high-level idea of website structure that we are thinking of, which is in the attached files. Logo is included as well. The final design would ideally be energy and analytics focused. We will need the new website to be coded as well, please.

Target Market(s)

Energy and utility industry

Industry/Entity Type

Energy/analytics

Coding

Coded - Design and coding required

Number of Pages Required

5+ page

Font styles to use
Sans Serif

Colors
0094D4
00A9DD
6FCCEA
C7EBF8
E9F6FB
F0912C
F2A743
F7CA91
FBE8D2
FDF5EE

Requirements
Must have
• Consistent color scheme- please use the one that we provided. We need an overview, a home page, and our core services. A separate job application page. Logo must be incorporated. We would like e "Meet our Team" page. Please include all of the content that is listed in our attachments.
Nice to have
• Movement
Should not have
• No music, no cartoons/animation, no pictures of a chalkboard

```html
<!DOCTYPE html>
<html lang="en">
<head>
<meta charset="utf-8">
<title>Harrow Point Metrics</title>
<link rel="stylesheet" href="https://fonts.googleapis.com/css2?family=Exo+2:wght@400;600;700&family=Roboto:wght@400;500;700&display=swap">
<style>
:root{
  --blue:#0094D4;
  --blue-2:#00A9DD;
  --blue-3:#6FCCEA;
  --blue-4:#C7EBF8;
  --blue-5:#E9F6FB;
  --orange:#F0912C;
  --orange-2:#F2A743;
  --orange-3:#F7CA91;
  --ink:#222;
  --body:#444;
  --footer:#2b2b2b;
}
*{box-sizing:border-box;margin:0;padding:0}
html,body{width:1200px;height:3316px;overflow:hidden;background:#fff}
body{position:relative;font-family:"Roboto",sans-serif;color:var(--body)}
.abs{position:absolute}
.btn{position:absolute;display:flex;align-items:center;justify-content:center;border-radius:24px;color:#fff;font-family:"Exo 2",sans-serif;font-weight:700;font-size:16px;background:var(--orange)}
.btn.blue{background:var(--blue)}
.heading{font-family:"Exo 2",sans-serif;font-weight:700;color:var(--blue)}
.heading .accent{color:var(--orange)}

/* header */
.site-header{top:0;left:0;width:1200px;height:88px;background:#fff}
.brand{position:absolute;display:flex;align-items:center;gap:10px}
.brand .mark{width:36px;height:36px;border-radius:50%;background:var(--blue-4)}
.brand .name{font-family:"Roboto",sans-serif;font-weight:400;font-size:27px;color:var(--blue);line-height:1;white-space:nowrap}
.main-nav{position:absolute;top:32px;font-size:17px;color:#444}
.main-nav span{position:absolute;white-space:nowrap}
.sub-nav{top:88px;left:0;width:1200px;height:50px;background:var(--orange);display:flex;align-items:center;padding-left:120px;gap:29px;color:#fff;font-size:13.5px;white-space:nowrap}

/* hero */
.hero{top:138px;left:0;width:1200px;height:600px;background:linear-gradient(100deg,#5fb6df 0%,#8ccbe8 35%,#c9e3ee 62%,#e6eef2 100%)}
.hero-text{left:110px;top:120px;color:#fff}
.hero-text .welcome{font-family:"Exo 2",sans-serif;font-size:41px;font-weight:400}
.hero-text h1{font-family:"Exo 2",sans-serif;font-weight:700;font-size:64px;line-height:77px;margin-top:6px}
.hero-text p{font-size:16px;line-height:27px;width:440px;margin-top:22px}
.dots{top:560px;left:553px;display:flex;gap:10px}
.dots i{display:block;width:24px;height:4px;background:#fff;border-radius:2px}
.dots i.on{background:var(--orange)}

/* about */
.about-photo{left:128px;top:827px;width:444px;height:444px;border-radius:50%;border:10px solid var(--blue);padding:6px;background:#fff}
.about-photo div{width:100%;height:100%;border-radius:50%;background:linear-gradient(135deg,#d9dee3,#9fb0c0 55%,#5d7187)}
.about-title{left:658px;top:875px;font-size:31px;white-space:nowrap}
.about-copy{left:658px;top:940px;width:426px;font-size:15.5px;line-height:25.8px;text-align:justify;color:#333}

/* services */
.services{top:1358px;left:0;width:1200px;height:660px;background:linear-gradient(180deg,#e4e7ea,#d3d9de 60%,#e2e5e8)}
.section-title{width:1200px;left:0;text-align:center;font-size:31px}
.card{position:absolute;top:176px;width:309px;height:381px;background:#fff;box-shadow:0 4px 14px rgba(0,0,0,.08);text-align:center}
.card .icon{width:125px;height:125px;border-radius:50%;margin:32px auto 0;box-shadow:0 2px 10px rgba(0,0,0,.12);display:flex;align-items:center;justify-content:center}
.card h3{font-family:"Roboto",sans-serif;font-weight:500;font-size:19.5px;color:#222;line-height:26px;margin-top:30px;padding:0 28px}
.card p{font-size:15px;line-height:23px;color:#444;margin-top:14px;padding:0 34px}
.card .more{position:absolute;bottom:26px;left:0;width:100%;font-family:"Exo 2",sans-serif;font-weight:700;font-size:15.5px;color:var(--orange)}
.arrow{position:absolute;width:52px;height:52px;border-radius:50%;display:flex;align-items:center;justify-content:center}
.connector{position:absolute;top:286px}

/* case studies */
.case{position:absolute;top:2186px;width:460px;height:329px;border:3px solid var(--blue);padding:34px 36px}
.case.alt{border-color:var(--orange)}
.case h3{font-family:"Exo 2",sans-serif;font-weight:700;font-size:31px;line-height:47px;color:var(--blue)}
.case.alt h3{color:var(--orange)}
.case p{font-size:15px;line-height:26px;color:#444;margin-top:22px}

/* band */
.band{top:2601px;left:0;width:1200px;height:472px;background:linear-gradient(90deg,#0a93d3 0%,#0a96d6 40%,#4db1e0 60%,#b9d9e8 80%,#e2e8ec 100%)}
.band h2{position:absolute;left:111px;top:82px;font-family:"Exo 2",sans-serif;font-weight:700;font-size:31px;color:#fff}
.band ul{position:absolute;left:112px;top:145px;list-style:none;color:#fff;font-size:15.5px}
.band li{display:flex;align-items:center;gap:9px;height:29px;white-space:nowrap}
.band li b{font-weight:700}
.tick{flex:none;width:14px;height:14px;border-radius:50%;background:var(--orange);display:flex;align-items:center;justify-content:center}

/* footer */
.site-footer{top:3073px;left:0;width:1200px;height:243px;background:var(--footer)}
.site-footer .brand .name{color:#fff;font-size:23px}
.site-footer .brand .mark{background:#555}
.foot-nav{position:absolute;top:104px;left:453px;display:flex;gap:40px;color:#fff;font-weight:700;font-size:14px}
.foot-rule{position:absolute;left:451px;top:142px;width:637px;height:1px;background:#666}
.social{position:absolute;top:160px;left:451px;display:flex;gap:6px}
.social i{display:block;width:37px;height:37px;border-radius:50%;border:2px solid var(--orange)}
.copy{position:absolute;right:112px;top:170px;color:#fff;font-size:14px}
</style>
</head>
<body>

<header class="abs site-header">
  <div class="brand" style="left:112px;top:24px">
    <span class="mark"></span>
    <span class="name">Harrow Point Metrics</span>
  </div>
  <nav class="main-nav">
    <span style="left:553px">Core Services</span>
    <span style="left:703px">About</span>
    <span style="left:797px">Our Work</span>
    <span style="left:918px">Blog</span>
    <span style="left:1001px">Contatc Us</span>
  </nav>
</header>

<nav class="abs sub-nav">
  <span>Forecating &amp; Perdictive Analytics</span>
  <span>T&amp;D Planning</span>
  <span>Evaluation</span>
  <span>Pilot&amp; Emerging Tech Support</span>
  <span>Program &amp; Portfolio Resource Planning</span>
  <span>More &#8964;</span>
</nav>

<section class="abs hero" role="img" aria-label="Laptop showing an energy analytics dashboard on a light blue backdrop">
  <div class="abs hero-text">
    <div class="welcome">Welcome to</div>
    <h1>Harrow Point<br>Metrics</h1>
    <p>Harrow Point Metrics was formed in 2016 to help utilities and regulatory agencies navigate the</p>
  </div>
  <a class="btn" style="left:110px;top:425px;width:144px;height:51px">Get Started</a>
  <div class="abs dots"><i></i><i class="on"></i><i></i></div>
</section>

<section>
  <div class="abs about-photo"><div role="img" aria-label="Two colleagues reviewing charts on a laptop"></div></div>
  <h2 class="abs heading about-title">About Harrow Point <span class="accent">Metrics</span></h2>
  <p class="abs about-copy">Harrow Point Metrics was formed in 2016 to help utilities and regulatory agencies navigate the technical, economic, and policy challenges of building a smarter and cleaner energy future. Through cutting edge research design and analysis methods we provide DSM program administrators with data-driven insights into how various technologies and interventions affect the way homes and businesses use energy.</p>
  <a class="btn" style="left:658px;top:1176px;width:120px;height:40px;font-size:15px">Learn More</a>
</section>

<section class="abs services" role="img" aria-label="Faded photo of an analyst at a desk with printed charts">
  <h2 class="abs heading section-title" style="top:95px">Our <span class="accent">Services</span></h2>

  <div class="arrow" style="left:41px;top:340px;background:var(--orange)">
    <svg width="18" height="24" viewBox="0 0 18 24"><path d="M13 3 4 12l9 9" fill="none" stroke="#fff" stroke-width="3" stroke-linecap="round"/></svg>
  </div>
  <div class="arrow" style="left:1108px;top:340px;border:2px solid var(--orange);background:#fff">
    <svg width="18" height="24" viewBox="0 0 18 24"><path d="M5 3l9 9-9 9" fill="none" stroke="var(--orange)" stroke-width="2.5" stroke-linecap="round"/></svg>
  </div>

  <div class="card" style="left:115px">
    <div class="icon">
      <svg width="62" height="62" viewBox="0 0 62 62" fill="none" stroke="var(--blue)" stroke-width="2"><rect x="3" y="20" width="56" height="32" rx="2"/><path d="M8 44l12-10 10 6 12-12 12 6"/><rect x="14" y="8" width="6" height="12"/><rect x="24" y="4" width="6" height="16"/><rect x="34" y="10" width="6" height="10"/><circle cx="50" cy="10" r="7"/><path d="M50 3v7h7"/><path d="M24 52v6h14v-6"/></svg>
    </div>
    <h3>Predictive Analytics and Forecasting</h3>
    <p>Distributed energy resource integration into planning and operations</p>
    <span class="more">Learn More &#8594;</span>
  </div>

  <div class="card" style="left:446px">
    <div class="icon">
      <svg width="62" height="62" viewBox="0 0 62 62" fill="none" stroke="var(--blue)" stroke-width="2"><circle cx="24" cy="20" r="6"/><circle cx="24" cy="20" r="11" stroke-dasharray="4 3"/><circle cx="46" cy="10" r="3"/><circle cx="48" cy="22" r="3"/><circle cx="44" cy="34" r="3"/><path d="M35 20h10M34 13l9-3M34 27l8 6"/><path d="M4 46l10-6h14l6 4h-12M14 56l8-4h16l18-12"/></svg>
    </div>
    <h3>T&amp;D Planning</h3>
    <p>Location specific, probabilistic forecasting for system, transmission and distribution planning (electric and gas)</p>
    <span class="more">Learn More &#8594;</span>
  </div>

  <div class="card" style="left:778px">
    <div class="icon">
      <svg width="62" height="62" viewBox="0 0 62 62" fill="none" stroke="var(--blue)" stroke-width="2"><rect x="10" y="6" width="36" height="46" rx="2"/><path d="M16 14h24M16 20h16"/><circle cx="32" cy="34" r="10"/><path d="M27 34l4 4 6-7M39 41l12 12"/></svg>
    </div>
    <h3>Evaluation</h3>
    <p>Expertise in demand response evaluations. Our team members are at the forefront of significant developments in DR pilots and</p>
    <span class="more">Learn More &#8594;</span>
  </div>

  <svg class="connector" style="left:404px" width="70" height="20" viewBox="0 0 70 20"><path d="M2 12q30 12 62-4" fill="none" stroke="#777"/><path d="M58 4l6 4-6 3" fill="none" stroke="#777"/></svg>
  <svg class="connector" style="left:735px" width="70" height="20" viewBox="0 0 70 20"><path d="M2 12q30-14 62-2" fill="none" stroke="#777"/><path d="M58 6l6 4-6 4" fill="none" stroke="#777"/></svg>
</section>

<section>
  <h2 class="abs heading section-title" style="top:2095px">Case <span class="accent">Studies</span></h2>
  <div class="case" style="left:109px">
    <h3>Journal Articles and Conference Presentations</h3>
    <p>Lorem ipsum dolor sit amet, consectetur adipiscing elit, sed do eiusmod</p>
    <a class="btn" style="left:36px;top:238px;width:120px;height:41px;font-size:15px">Learn More</a>
  </div>
  <div class="case alt" style="left:628px">
    <h3>Published Reports</h3>
    <p>Lorem ipsum dolor sit amet, consectetur adipiscing elit, sed do eiusmod tempor incididunt ut labore et dolore magna aliqua Ut enim ad minim veniam, quis nostrud exercitation.</p>
    <a class="btn blue" style="left:36px;top:238px;width:120px;height:41px;font-size:15px">Learn More</a>
  </div>
</section>

<section class="abs band" role="img" aria-label="Hands typing at a keyboard beside an analytics dashboard">
  <h2>About Harrow Point Metrics</h2>
  <ul>
    <li><span class="tick"><svg width="8" height="8" viewBox="0 0 8 8"><path d="M1 4l2 2 4-4" fill="none" stroke="#fff" stroke-width="1.5"/></svg></span><span>Predictive Analytics and Forecasting</span></li>
    <li><span class="tick"><svg width="8" height="8" viewBox="0 0 8 8"><path d="M1 4l2 2 4-4" fill="none" stroke="#fff" stroke-width="1.5"/></svg></span><span>T&amp;D Planning – <b>Northgate Energy or Valley Crest Power?</b></span></li>
    <li><span class="tick"><svg width="8" height="8" viewBox="0 0 8 8"><path d="M1 4l2 2 4-4" fill="none" stroke="#fff" stroke-width="1.5"/></svg></span><span>Evaluation – <b>WCE? RMG&amp;E? Different state?</b></span></li>
    <li><span class="tick"><svg width="8" height="8" viewBox="0 0 8 8"><path d="M1 4l2 2 4-4" fill="none" stroke="#fff" stroke-width="1.5"/></svg></span><span>Pilot &amp; Emerging Tech Support – <b>Ag DR Study? LVP&amp;E Battery Pilot?</b></span></li>
    <li><span class="tick"><svg width="8" height="8" viewBox="0 0 8 8"><path d="M1 4l2 2 4-4" fill="none" stroke="#fff" stroke-width="1.5"/></svg></span><span>Program Portfolio &amp; Resource Planning – <b>PA Work?</b></span></li>
    <li><span class="tick"><svg width="8" height="8" viewBox="0 0 8 8"><path d="M1 4l2 2 4-4" fill="none" stroke="#fff" stroke-width="1.5"/></svg></span><span>Program Delivery Support – <b>CRPC?</b></span></li>
  </ul>
  <a class="btn" style="left:113px;top:344px;width:120px;height:41px;font-size:15px">Learn More</a>
</section>

<footer class="abs site-footer">
  <div class="brand" style="left:118px;top:126px">
    <span class="mark"></span>
    <span class="name">Harrow Point Metrics</span>
  </div>
  <nav class="foot-nav"><span>Core Services</span><span>About</span><span>Our Work</span><span>Blog</span><span>Contatc Us</span></nav>
  <div class="foot-rule"></div>
  <div class="social"><i></i><i></i><i></i></div>
  <div class="copy">© 2022 Harrowpointmetrics. All Right Reserved.</div>
</footer>

</body>
</html>
```